Letter and Envelope Design For Harborline Realty

Please design a letter and an envelope incorporating our logo (See Attached). We are also launched a business card contest. Since we want them to match, please feel free to submit a design for both the business card and also the letter design and envelope.

Requirements
Must have
• The envelope, the letter and the business cards must match somehow connecting the designs. We want them to have something that holds them together besides the logo.

```html
<!DOCTYPE html>
<html lang="en">
<head>
<meta charset="utf-8">
<title>Harborline Realty – Letterhead and Envelope</title>
<link href="https://fonts.googleapis.com/css2?family=Montserrat:wght@600&family=Roboto:wght@400;500&family=Allura&display=swap" rel="stylesheet">
<style>
:root{
  --backdrop:#676767;
  --paper:#f6f6f6;
  --navy:#0b1a8c;
  --slate:#5e5e5e;
  --ink:#333;
  --muted:#777;
  --ghost:#e9e9e9;
}
*{box-sizing:border-box;margin:0;padding:0}
html,body{width:1200px;height:816px;overflow:hidden;background:var(--backdrop)}
body{font-family:'Roboto',Arial,sans-serif}
.stage{position:relative;width:1500px;height:1020px;transform:scale(.8);transform-origin:0 0}
.sheet{position:absolute;background:var(--paper);overflow:hidden}
.sheet svg.deco{position:absolute;left:0;top:0}
.brand{font-family:'Montserrat',Arial,sans-serif;font-weight:600;color:var(--navy);letter-spacing:2px;text-transform:uppercase;line-height:1.15}
.brand-dot{border:2px solid var(--navy);border-radius:50%}

/* envelope front */
.envelope-front{left:97px;top:276px;width:592px;height:265px}
.envelope-front .brand-dot{position:absolute;left:28px;top:36px;width:42px;height:42px}
.envelope-front .brand{position:absolute;left:82px;top:40px;font-size:15px}
.envelope-front .return-address{position:absolute;left:43px;top:88px;font-size:8.5px;color:var(--ink)}

/* envelope back */
.envelope-back{left:97px;top:571px;width:592px;height:264px}
.envelope-back .brand{position:absolute;left:0;width:592px;top:31px;text-align:center;color:#fff;font-size:14px}

/* letterhead */
.letterhead{left:756px;top:162px;width:489px;height:693px;color:var(--muted)}
.letterhead .brand-dot{position:absolute;left:367px;top:56px;width:50px;height:50px}
.letterhead .brand{position:absolute;left:292px;width:200px;top:111px;text-align:center;font-size:15px}
.letter-body{position:absolute;left:31px;top:131px;width:428px;font-size:7.6px;line-height:11.1px}
.letter-body .date{margin-bottom:25px}
.letter-body .recipient strong{color:var(--ink);font-weight:500}
.letter-body .recipient{margin-bottom:18px}
.letter-body .salutation{margin-bottom:11px}
.letter-body p.copy{text-align:justify;margin-bottom:11px}
.sign-off{position:absolute;left:31px;top:510px;font-size:7.6px}
.sign-off .name{color:var(--ink);font-weight:500}
.sign-off .signature{font-family:'Allura',cursive;font-size:22px;color:#3040a0;margin:2px 0 4px}
.contact{position:absolute;left:31px;top:621px;font-size:8.5px;color:var(--ink);line-height:12.5px;list-style:none}
.contact li{display:flex;align-items:center;gap:5px}
.contact svg{width:8px;height:8px;fill:var(--navy)}
.contact .gap{margin-left:4px}
</style>
</head>
<body>
<div class="stage">

  <section class="sheet envelope-front" aria-label="Envelope front">
    <svg class="deco" width="592" height="265" viewBox="0 0 592 265">
      <circle cx="498" cy="122" r="155" fill="none" stroke="var(--ghost)" stroke-width="14"/>
      <path d="M55 0H592V31Q380 10 55 0Z" fill="var(--navy)"/>
      <path d="M170 9Q420 22 592 31V52Q420 24 170 9Z" fill="var(--slate)"/>
    </svg>
    <div class="brand-dot"></div>
    <div class="brand">Harborline<br>Realty</div>
    <p class="return-address">234 Anywhere, Any City, Any Town, US 1234</p>
  </section>

  <section class="sheet envelope-back" aria-label="Envelope back">
    <svg class="deco" width="592" height="264" viewBox="0 0 592 264">
      <path d="M0 0H592L552 76Q542 95 515 95H77Q50 95 40 76Z" fill="var(--navy)"/>
      <circle cx="297" cy="46" r="35" fill="none" stroke="#2336a0" stroke-width="2"/>
    </svg>
    <div class="brand">Harborline Realty</div>
  </section>

  <section class="sheet letterhead" aria-label="Letterhead">
    <svg class="deco" width="489" height="693" viewBox="0 0 489 693">
      <circle cx="244" cy="348" r="150" fill="none" stroke="var(--ghost)" stroke-width="10"/>
      <path d="M0 0H489Q300 6 0 33Z" fill="var(--navy)"/>
      <path d="M0 39Q200 14 380 9Q200 22 0 53Z" fill="var(--slate)"/>
    </svg>
    <div class="brand-dot"></div>
    <div class="brand">Harborline<br>Realty</div>

    <div class="letter-body">
      <p class="date">30/20/2016</p>
      <p class="recipient"><strong>Mr. XYZ Smith</strong><br>123, Street No. 123,<br>City Name<br>Pincode-123456</p>
      <p class="salutation">Dear Sir,</p>
      <p class="copy">Lorem Ipsum is simply dummy text of the printing and typesetting industry. Lorem Ipsum has been the industry's standard dummy text ever since the 1500s, when an unknown printer took a galley of type and scrambled it to make a type specimen book. It has survived not only five centuries, but also the leap into electronic typesetting, remaining essentially unchanged. It was popularised in the 1960s with the release of Trandell sheets containing Lorem Ipsum passages, and more recently with desktop publishing software like Quillset Layout including versions of Lorem Ipsum.</p>
      <p class="copy">Lorem Ipsum is simply dummy text of the printing and typesetting industry. Lorem Ipsum has been the industry's standard dummy text ever since the 1500s, when an unknown printer took a galley of type and scrambled it to make a type specimen book. It has survived not only five centuries, but also the leap into electronic typesetting, remaining essentially unchanged. It was popularised in the 1960s with the release of Trandell sheets containing Lorem Ipsum passages, and more recently with desktop publishing software like Quillset Layout including versions of Lorem Ipsum.</p>
      <p class="copy">Lorem Ipsum is simply dummy text of the printing and typesetting industry. Lorem Ipsum has been the industry's standard dummy text ever since the 1500s, when an unknown printer took a galley of type and scrambled it to make a type specimen book.</p>
      <p class="copy">Lorem Ipsum is simply dummy text of the printing and typesetting industry. Lorem Ipsum has been the industry's standard dummy text ever since the 1500s, when an unknown printer took a galley of type and scrambled it to make a type specimen book.</p>
    </div>

    <div class="sign-off">
      <p class="name">Your Name</p>
      <p class="signature">Your Signature</p>
      <p>CEO &nbsp;|&nbsp; Owner</p>
    </div>

    <ul class="contact">
      <li><svg viewBox="0 0 10 10"><path d="M2 0L4 2.5L3 3.8Q4.2 6 6.2 7L7.5 6L10 8L8.5 10Q3 9.5 0 1.5Z"/></svg>555.555.5555</li>
      <li><svg viewBox="0 0 10 10"><circle cx="5" cy="5" r="4.5" fill="none" stroke="var(--navy)" stroke-width="1.2"/><path d="M0.5 5H9.5M5 0.5V9.5" stroke="var(--navy)" stroke-width="1"/></svg>johndoe@yourwebsite.com
        <svg class="gap" viewBox="0 0 10 10"><rect x="0" y="1" width="10" height="8" rx="1"/><path d="M0.5 1.8L5 5.5L9.5 1.8" fill="none" stroke="#fff" stroke-width="1"/></svg>www.yourwebsite.com</li>
      <li><svg viewBox="0 0 10 10"><path d="M5 10Q1 5.5 1 4A4 4 0 0 1 9 4Q9 5.5 5 10Z"/><circle cx="5" cy="4" r="1.4" fill="#fff"/></svg>234 Anywhere, Any City, Any Town, US 1234</li>
    </ul>
  </section>

</div>
</body>
</html>
```